Fenlow Systems

Looking for a web site design to market our services/applications
We write and supply bespoke web applications for the offshore and construction industries
Our initial product is Tolv - rope access equipment management
Our buyers will be Rope Access companies via trade associations such as KOBEN and DULMO
we have a logo designed see it attached we would like to see crisp professional designs based around these colours and design
we will supply web copy later
looking for home, services, blog, contact us, order and a general template (privacy, site map, T&C) pages
Updates
This payment will be for the homepage only
We can discuss other options (pages) with the successful designer
Regards
Marcus
Industry/Entity Type
Construction
Look and feel
Each slider illustrates characteristics of the customer's brand and the style your logo design should communicate.

```html
<!DOCTYPE html>
<html lang="en">
<head>
<meta charset="utf-8">
<title>Fenlow Systems</title>
<link href="https://fonts.googleapis.com/css2?family=Exo+2:wght@400;500&family=Open+Sans:wght@400;600&family=Raleway:wght@400;500&display=swap" rel="stylesheet">
<style>
:root{
  --navy:#1f2f8f;
  --navy-dark:#0d1f73;
  --sky:#1d9ad9;
  --sky-bar:#1b92d8;
  --grey-bg:#ebebeb;
  --footer-bg:#f4f4f4;
  --text:#333;
  --muted:#8a8a8a;
  --red:#d9342b;
  --tag-mid:#6f8c96;
  --tag-dark:#2b2b2b;
}
*{margin:0;padding:0;box-sizing:border-box}
html,body{width:857px;height:1200px;overflow:hidden}
body{position:relative;background:#fff;font-family:"Open Sans",sans-serif;color:var(--text)}
.abs{position:absolute}
.header-band{left:0;top:0;width:857px;height:462px;background:var(--grey-bg);border-top:1px solid var(--sky)}
.brand-mark{left:74px;top:18px;width:44px;height:44px;border-radius:6px;background:var(--navy)}
.brand-rule{left:127px;top:10px;width:1px;height:62px;background:#d4d4d4}
.brand-name{left:135px;top:24px;font-family:"Open Sans",sans-serif;font-weight:600;font-size:16px;line-height:16px;color:var(--navy)}
.nav-item{top:28px;text-align:center;font-family:"Open Sans",sans-serif;font-size:11.5px;color:var(--muted);transform:translateX(-50%)}
.nav-item svg{display:block;margin:0 auto 3px}
.nav-item.active{color:var(--navy)}
.nav-rule{top:32px;width:1px;height:26px;background:#cfcfcf}
.hero{left:70px;top:81px;width:715px;height:381px;background:linear-gradient(120deg,#dde4ea 0%,#b9c6d2 35%,#eef2f5 60%,#c9d2da 80%,#e8c347 100%)}
.hero-arrow{top:259px;width:24px;height:24px;border-radius:50%;background:#555c63;opacity:.85}
.cap{left:122px;height:31px;color:#fff;font-family:"Open Sans",sans-serif;font-size:16.5px;line-height:31px;padding:0 12px}
.cap.one{top:346px;width:172px;background:var(--navy)}
.cap.two{top:382px;width:347px;background:var(--sky);font-size:15px}
.section-title{left:0;width:857px;text-align:center;font-family:"Exo 2",sans-serif;font-size:19.5px;color:var(--navy);letter-spacing:.5px}
.section-title span{color:#333}
.intro{left:80px;top:535px;width:697px;text-align:center;font-size:9.2px;line-height:13px;color:#444}
.intro-sub{left:0;top:562px;width:857px;text-align:center;font-size:11px;color:#444}
.service{top:617px;width:170px}
.service-icon{position:absolute;left:0;top:0;width:37px;height:36px;background:var(--sky)}
.service-icon::after{content:"";position:absolute;left:14px;bottom:-5px;border:5px solid transparent;border-bottom:0;border-top-color:var(--sky)}
.service-icon svg{position:absolute;left:9px;top:8px}
.service-title{position:absolute;left:49px;top:0;font-family:"Raleway",sans-serif;font-size:11px;line-height:17px;color:#222;width:120px}
.service-body{position:absolute;left:0;top:55px;width:170px;font-family:"Raleway",sans-serif;font-size:8.3px;line-height:13.5px;color:#333}
.service-link{position:absolute;left:0;top:96px;font-family:"Raleway",sans-serif;font-size:8.3px;color:var(--red)}
.post-img{top:814px;width:100px;height:104px}
.post-title{top:813px;width:215px;font-size:10.4px;line-height:13px;color:#111}
.post-body{top:840px;width:220px;font-size:8.6px;line-height:10.6px;color:#333}
.tag{top:904px;height:13px;font-size:7px;font-weight:600;line-height:13px;color:#fff;text-align:center}
.tag.date{width:54px;background:var(--navy-dark);border-bottom:2px solid var(--sky)}
.tag.count{width:26px;background:var(--tag-mid)}
.tag.more{width:49px;background:var(--tag-dark)}
.footer{left:0;top:984px;width:857px;height:176px;background:var(--footer-bg);box-shadow:inset 0 6px 6px -4px rgba(0,0,0,.12)}
.f-head{top:1008px;font-size:11px;color:#222;letter-spacing:.3px}
.f-rule{top:1008px;width:1px;height:124px;background:#dedede}
.f-nav{left:72px;top:1036px;list-style:none;font-size:9.2px;color:#444;line-height:15.5px}
.f-nav li::before{content:"›";display:inline-block;width:12px;color:#666}
.f-addr{left:274px;top:1036px;font-size:9px;line-height:13.3px;color:#444}
.field{left:473px;width:132px;background:#fff;border:1px solid #c9c9c9;font-size:7.5px;color:#444;padding:2px 5px}
.btn{left:473px;top:1121px;width:132px;height:19px;background:var(--navy-dark);color:#fff;font-size:8.5px;line-height:19px;text-align:center}
.badge-a{left:683px;top:1040px;width:104px;height:34px;border-radius:4px;background:#1c1c1c}
.badge-b{left:695px;top:1083px;width:82px;height:52px;border-radius:50%;background:#fff;border:4px solid var(--navy-dark)}
.bottom-bar{left:0;top:1160px;width:857px;height:40px;background:var(--sky-bar)}
.legal{left:74px;top:1175px;font-size:9.4px;color:#fff}
.legal span{margin:0 9px}
.social{top:1175px;width:13px;height:13px;border-radius:50%;background:#fff}
</style>
</head>
<body>
<div class="abs header-band"></div>

<div class="abs brand-mark"></div>
<div class="abs brand-rule"></div>
<div class="abs brand-name">Fenlow<br>Systems</div>

<nav>
  <div class="abs nav-item active" style="left:466px">
    <svg width="12" height="11" viewBox="0 0 12 11"><path d="M6 0L0 4h12z M1 5h10v6H1z" fill="#1f2f8f"/></svg>Home</div>
  <div class="abs nav-rule" style="left:502px"></div>
  <div class="abs nav-item" style="left:541px">
    <svg width="12" height="11" viewBox="0 0 12 11"><path d="M1 1l10 9M11 1L1 10" stroke="#9a9a9a" stroke-width="2"/></svg>Services</div>
  <div class="abs nav-rule" style="left:582px"></div>
  <div class="abs nav-item" style="left:613px">
    <svg width="14" height="11" viewBox="0 0 14 11"><path d="M1 4h4l7-3v9L5 7H1z" fill="#9a9a9a"/></svg>Blog</div>
  <div class="abs nav-rule" style="left:645px"></div>
  <div class="abs nav-item" style="left:678px">
    <svg width="11" height="12" viewBox="0 0 11 12"><rect x="1" y="1" width="9" height="10" fill="none" stroke="#9a9a9a" stroke-width="1.4"/><path d="M3 4h5M3 6h5M3 8h5" stroke="#9a9a9a"/></svg>Order</div>
  <div class="abs nav-rule" style="left:714px"></div>
  <div class="abs nav-item" style="left:760px">
    <svg width="10" height="12" viewBox="0 0 10 12"><path d="M2 1l2 3-1 1q1 3 3 4l1-1 2 2-2 2Q1 10 1 2z" fill="#9a9a9a"/></svg>Contact Us</div>
</nav>

<div class="abs hero" role="img" aria-label="Photo of engineers talking in an office behind a desk with plans, glasses, a ruler and a yellow hard hat"></div>
<div class="abs hero-arrow" style="left:89px"><svg width="24" height="24"><path d="M14 7l-5 5 5 5" stroke="#fff" stroke-width="2.5" fill="none"/></svg></div>
<div class="abs hero-arrow" style="left:743px"><svg width="24" height="24"><path d="M10 7l5 5-5 5" stroke="#fff" stroke-width="2.5" fill="none"/></svg></div>
<div class="abs cap one">Fenlow Systems</div>
<div class="abs cap two">TOLV - Rope access equipment management</div>

<h1 class="abs section-title" style="top:496px;font-weight:400">FENLOW SYSTEMS <span>- WHO WE ARE</span></h1>
<p class="abs intro">We have a strong team of experienced developers and also understand the challenges faced by online projects – We are very competitive with our quotations and produce high quality outcomes for our clients. Our engagement model is to understand your requirements and providing cost effective development resources so</p>
<p class="abs intro-sub">Our Core services Are</p>

<div class="abs service" style="left:77px">
  <div class="service-icon"><svg width="19" height="19" viewBox="0 0 19 19"><circle cx="9.5" cy="9.5" r="8" fill="#fff"/><path d="M5 6q3-1 4 2t4 2M7 14q1-3 4-2" stroke="#1d9ad9" stroke-width="1.5" fill="none"/></svg></div>
  <div class="service-title">Lorem ipsum<br>Sit Amit</div>
  <div class="service-body">Vestibulum ante ipsum primis in faucibus orci luctus et ultrices posuere cubilia.</div>
  <div class="service-link">Details</div>
</div>
<div class="abs service" style="left:264px">
  <div class="service-icon"><svg width="19" height="19" viewBox="0 0 19 19"><circle cx="9.5" cy="8" r="4" fill="none" stroke="#fff" stroke-width="1.5"/><path d="M8 13h3v3H8zM9.5 0v2M2 8h2M15 8h2M4 3l1.5 1.5M15 3l-1.5 1.5" stroke="#fff" stroke-width="1.5"/></svg></div>
  <div class="service-title">Contantry Popilar</div>
  <div class="service-body">Suspendisse in sapien auctor sapien vulputate porttitor. Integer lacinia.</div>
  <div class="service-link">Details</div>
</div>
<div class="abs service" style="left:451px">
  <div class="service-icon"><svg width="19" height="19" viewBox="0 0 19 19"><path d="M2 17l4-1 11-11-3-3L3 13z" fill="#fff"/><path d="M3 9l2-2 6 6-2 2z" fill="#fff"/></svg></div>
  <div class="service-title">Ipsum Dolor Sit<br>Contantry Popilar</div>
  <div class="service-body">Etiam in tincidunt arcu, at tempor magna. Maecenas ut odio nunc.</div>
  <div class="service-link">Details</div>
</div>
<div class="abs service" style="left:638px">
  <div class="service-icon"><svg width="19" height="19" viewBox="0 0 19 19"><path d="M3 9a6.5 6.5 0 0 1 11.5-4M16 10a6.5 6.5 0 0 1-11.5 4" stroke="#fff" stroke-width="2.2" fill="none"/><path d="M16 1v5h-5zM3 18v-5h5z" fill="#fff"/></svg></div>
  <div class="service-title">Popilar Sit Amit</div>
  <div class="service-body">Aliquam convallis vitae metus ut luctus. Nulla vestibulum consequat.</div>
  <div class="service-link">Details</div>
</div>

<h2 class="abs section-title" style="top:762px;font-weight:400">LATEST BLOG</h2>

<svg class="abs" style="left:28px;top:874px" width="12" height="18"><path d="M10 1L2 9l8 8" stroke="#999" stroke-width="1.5" fill="none"/></svg>
<svg class="abs" style="left:819px;top:874px" width="12" height="18"><path d="M2 1l8 8-8 8" stroke="#999" stroke-width="1.5" fill="none"/></svg>

<div class="abs post-img" style="left:72px;background:linear-gradient(135deg,#f2f2f2 0%,#e9b93a 40%,#f4f4f4 75%,#d9d9d9 100%)" role="img" aria-label="Yellow hard hat resting on construction plans with a pen"></div>
<h3 class="abs post-title" style="left:186px;font-weight:400">Harbeck Financial Group Participating in the 2014 Coastline Golf Tournament</h3>
<p class="abs post-body" style="left:186px">mollis varius dolor id, varius molestie urna. Cras id tellus nisl. Fusce purus ante, elementum id metus eget, congue pharetra dolor. Sed non mollis quam. Nulla non eros diam.</p>
<div class="abs tag date" style="left:186px">05 june 15</div>
<div class="abs tag count" style="left:244px">12</div>
<div class="abs tag more" style="left:274px">Read More</div>

<div class="abs post-img" style="left:450px;background:linear-gradient(135deg,#e9ecef 0%,#3c4250 45%,#c9ced4 70%,#2b2f38 100%)" role="img" aria-label="Business people shaking hands in an office"></div>
<h3 class="abs post-title" style="left:564px;font-weight:400">New Product: Foreign Exchange</h3>
<p class="abs post-body" style="left:564px;top:833px">mollis varius dolor id, varius molestie urna. Cras id tellus nisl. Fusce purus ante, elementum id metus eget, congue pharetra dolor. Sed non mollis quam. Nulla non eros diam. Proin ultricies, felis eget sceler-isque</p>
<div class="abs tag date" style="left:564px">05 june 15</div>
<div class="abs tag count" style="left:622px">12</div>
<div class="abs tag more" style="left:652px">Read More</div>

<footer>
  <div class="abs footer"></div>
  <div class="abs f-head" style="left:72px">NAVIGATION</div>
  <div class="abs f-rule" style="left:210px"></div>
  <ul class="abs f-nav"><li>Home</li><li>Services,</li><li>Blog</li><li>Order</li><li>Contact us</li></ul>

  <div class="abs f-head" style="left:256px">ADDRESS</div>
  <svg class="abs" style="left:258px;top:1039px" width="8" height="11" viewBox="0 0 8 11"><path d="M4 11L1 5a3 3 0 1 1 6 0z" fill="#999"/><circle cx="4" cy="4" r="1.2" fill="#fff"/></svg>
  <div class="abs f-addr">PO Box 412<br>27 Marlow Street<br>Kestrel Bay<br>Northern Territory 0862</div>
  <div class="abs f-rule" style="left:417px"></div>

  <div class="abs f-head" style="left:474px">CONTACT</div>
  <div class="abs field" style="top:1039px;height:16px">Name</div>
  <div class="abs field" style="top:1061px;height:16px">Email</div>
  <div class="abs field" style="top:1082px;height:30px">Message</div>
  <div class="abs btn">CONTACT NOW</div>
  <div class="abs f-rule" style="left:617px"></div>

  <div class="abs badge-a" role="img" aria-label="DULMO trade association badge"></div>
  <div class="abs badge-b" role="img" aria-label="KOBEN trade association badge"></div>

  <div class="abs bottom-bar"></div>
  <div class="abs legal">Copyright © yourwebsite<span>|</span>Privacy<span>|</span>Sitemap<span>|</span>T&amp;C</div>
  <div class="abs social" style="left:687px" aria-label="Social link"></div>
  <div class="abs social" style="left:719px" aria-label="Social link"></div>
  <div class="abs social" style="left:749px" aria-label="Social link"></div>
  <div class="abs social" style="left:777px" aria-label="Social link"></div>
</footer>
</body>
</html>
```